LM-Steuerberatung WordPress Site fully implemented (tax advisor)

Hello!
I need a little Wordpress Site for my newly founded Tax-Advisor Company.
I am a one-man Office advising in the area of Crypto-Currency.
PLEASE only provide a Design, if you can also Implement a WP-Site afterwards on an existing Webspace.

Please find the Content and Website-Description in the attached Document

Language for the Website is German (for now)

Target Market(s)

Tax-Advisory (specialized in Crypto Currency)

Coding

Coded - Design and coding required

Number of Pages Required

5+ page

Font styles to use
Sans Serif

Requirements
Must have
• Wordpress Implementation afterwards - Details according to attached Project Information Document

```html
<!DOCTYPE html>
<html lang="de">
<head>
<meta charset="utf-8">
<title>Über mich – LM-Steuerberatung</title>
<link rel="stylesheet" href="https://fonts.googleapis.com/css2?family=Poppins:wght@400;500;600;700&family=Caveat:wght@600&display=swap">
<style>
:root{
  --navy:#1b2438;
  --navy-deep:#131c33;
  --text:#5f6672;
  --muted:#9aa0a8;
  --badge-gray:#a3a3a3;
  --light:#f4f4f5;
  --line:#cfd1d4;
  --white:#ffffff;
}
*{box-sizing:border-box;margin:0;padding:0}
html,body{width:1200px;height:2208px;overflow:hidden}
body{font-family:"Poppins",sans-serif;color:var(--text);background:var(--white);position:relative}
.container{position:absolute;left:93px;width:1014px}

/* top bar */
.topbar{position:absolute;top:0;left:0;width:1200px;height:44px;background:var(--navy);color:var(--white);font-size:14px}
.topbar .social{position:absolute;left:93px;top:0;height:44px;display:flex;align-items:center;gap:16px;font-size:11px;font-weight:600;letter-spacing:.5px}
.topbar .contact{position:absolute;right:93px;top:0;height:44px;display:flex;align-items:center;gap:18px}
.topbar .contact span{display:flex;align-items:center;gap:10px}
.topbar .divider{width:1px;height:24px;background:#4a5266}
.topbar b{font-weight:600}

/* nav */
.navbar{position:absolute;top:44px;left:0;width:1200px;height:76px;background:var(--white)}
.brand-tab{position:absolute;left:98px;top:44px;width:292px;height:91px;background:var(--white);clip-path:polygon(0 0,100% 0,100% 82%,94% 100%,6% 100%,0 82%);z-index:3}
.brand{position:absolute;left:110px;top:80px;display:flex;align-items:center;gap:10px;z-index:4;font-weight:600;font-size:17px;color:var(--navy);letter-spacing:.3px}
.brand .mark{width:16px;height:16px;background:var(--navy)}
.menu{position:absolute;top:44px;left:476px;height:76px;display:flex;align-items:center;gap:37px;font-size:15px;text-transform:uppercase;color:var(--text);z-index:4}
.menu .active{color:var(--navy);font-weight:500}
.btn-contact{position:absolute;left:949px;top:60px;width:157px;height:45px;border:2px solid var(--navy);border-radius:23px;display:flex;align-items:center;justify-content:center;gap:14px;font-weight:600;font-size:14px;color:var(--navy);letter-spacing:.6px;z-index:4}

/* hero */
.hero{position:absolute;top:120px;left:0;width:1200px;height:279px;background:linear-gradient(100deg,#4a4c54 0%,#6b4435 28%,#4a3a38 45%,#2a2f43 70%,#1b2236 100%)}
.hero h1{position:absolute;width:100%;top:117px;text-align:center;color:var(--white);font-size:38px;font-weight:700;letter-spacing:.5px}

/* about */
.portrait-ring{position:absolute;left:93px;top:483px;width:388px;height:388px;border-radius:50%;border:2px dotted var(--navy)}
.portrait-arc{position:absolute;left:108px;top:498px;width:358px;height:358px;border-radius:50%;border:2px solid #9ea2aa;border-top-color:transparent;transform:rotate(0deg)}
.portrait{position:absolute;left:125px;top:515px;width:324px;height:324px;border-radius:50%;background:radial-gradient(circle at 50% 40%,#d9dadb 0%,#c4c6c8 55%,#5a5b5f 100%);box-shadow:0 8px 14px rgba(0,0,0,.15)}
.name-badge{position:absolute;left:160px;top:897px;width:247px;height:70px;background:var(--navy);border-radius:6px;clip-path:polygon(0 0,100% 0,97% 10%,100% 100%,0 100%);color:var(--white);text-align:center;padding-top:8px}
.name-badge .name{font-family:"Caveat",cursive;font-size:27px;line-height:28px}
.name-badge .role{font-size:14px;letter-spacing:.6px;font-weight:500}
.about-text{position:absolute;left:556px;top:474px;width:550px;font-size:16.5px;line-height:32px;color:var(--text)}
.about-text p+p{margin-top:23px}

/* career */
.career{position:absolute;top:1054px;left:0;width:1200px;height:761px;background:var(--light)}
.col{position:absolute;top:80px}
.col.left{left:93px;width:474px}
.col.right{left:632px;width:475px}
.col h2{font-size:19.5px;font-weight:600;color:#5e6470;margin-bottom:26px}
.item{display:flex;gap:27px;padding:22px 0 30px;border-bottom:1px solid var(--line);font-size:16.5px;line-height:32px}
.item:first-of-type{padding-top:0}
.item:last-of-type{border-bottom:none}
.year{flex:none;height:41px;padding:0 17px;border-radius:6px;background:var(--navy);color:var(--white);font-weight:700;font-size:17px;line-height:41px;margin-top:8px;clip-path:polygon(0 0,100% 0,93% 24%,93% 100%,0 100%)}
.year.gray{background:var(--badge-gray)}
.rule{position:absolute;left:93px;top:575px;width:1014px;height:1px;background:var(--line)}
.btn-profile{position:absolute;left:444px;top:619px;width:313px;height:54px;border-radius:27px;background:var(--navy);color:var(--white);display:flex;align-items:center;justify-content:center;gap:16px;font-size:14px;font-weight:600}
.btn-profile .sep{width:1px;height:20px;background:#6b7386}

/* footer */
.footer{position:absolute;top:1815px;left:0;width:1200px;height:393px;background:radial-gradient(circle at 70% 60%,#1d2a4d 0%,var(--navy-deep) 70%);color:#8c93a6}
.footer .brand-foot{position:absolute;left:93px;top:108px;display:flex;align-items:center;gap:10px;font-weight:600;font-size:17px;color:var(--white)}
.footer .brand-foot .mark{width:16px;height:16px;background:var(--white)}
.footer .about{position:absolute;left:93px;top:154px;width:360px;font-size:16.5px;line-height:32px}
.footer .copy{position:absolute;left:93px;top:280px;font-size:15px}
.footer h3{font-size:18.5px;font-weight:600;color:var(--white);letter-spacing:.4px}
.quick{position:absolute;left:580px;top:88px}
.quick ul{list-style:none;margin-top:12px}
.quick li{font-size:16.5px;line-height:38px;display:flex;align-items:center;gap:12px}
.info{position:absolute;left:847px;top:88px;width:270px}
.info .row{display:flex;gap:22px;margin-top:18px;align-items:flex-start}
.info .icon{width:48px;height:40px;border-radius:4px;background:#d8dadd;display:flex;align-items:center;justify-content:center;clip-path:polygon(0 0,100% 0,94% 20%,94% 100%,0 100%)}
.info .label{font-size:16px;line-height:24px}
.info .value{font-size:16.5px;color:var(--white);line-height:26px}
.info .socials{margin-top:24px;font-size:16.5px;display:flex;gap:20px;align-items:center}
.info .socials span.net{font-size:11px;color:var(--white);font-weight:600}
</style>
</head>
<body>

<header class="topbar">
  <div class="social"><span>SOZIAL</span><span>KURZNETZ</span><span>PRONET</span></div>
  <div class="contact">
    <span><svg width="20" height="18" viewBox="0 0 20 18" fill="none" stroke="#fff" stroke-width="1.4"><rect x="1" y="5" width="18" height="12" rx="2"/><path d="M1 7l9 6 9-6M4 5V2h12v3"/></svg>Email: office@lm-kryptosteuer.at</span>
    <span class="divider"></span>
    <span><svg width="20" height="20" viewBox="0 0 20 20" fill="none" stroke="#fff" stroke-width="1.4"><path d="M4 2l3 3-2 3c1 2 3 4 5 5l3-2 3 3-2 3C8 16 3 11 2 4z"/></svg>Phone: <b>+43 512 000 471</b></span>
  </div>
</header>

<nav class="navbar"></nav>
<div class="brand-tab"></div>
<div class="brand"><span class="mark"></span>LM STEUERBERATUNG</div>
<div class="menu">
  <span>Home</span>
  <span>Leistungen ▾</span>
  <span class="active">Über mich</span>
  <span>Impressum</span>
</div>
<div class="btn-contact">KONTAKT
  <svg width="22" height="22" viewBox="0 0 22 22" fill="none" stroke="#1b2438" stroke-width="1.6"><path d="M8 5a8 8 0 1 1 0 12"/><path d="M2 11h11M9 7l4 4-4 4"/></svg>
</div>

<section class="hero" role="img" aria-label="Foto: Hand hält eine Ledergeldbörse mit Krypto-Münzen vor einem Laptop">
  <h1>ÜBER MICH</h1>
</section>

<div class="portrait-ring"></div>
<div class="portrait-arc"></div>
<div class="portrait" role="img" aria-label="Porträtfoto des Steuerberaters im grauen Sakko mit Smartphone"></div>
<div class="name-badge">
  <div class="name">Mag. Lukas Mahrer</div>
  <div class="role">Professional Tax Advisor</div>
</div>

<div class="about-text">
  <p>Mag. Lukas Mahrer Ich blicke auf eine sehr umfassende Ausbildung und langjährige Berufserfahrung in der IT Branche zurück. Nach Abschluss des Wirtschaftsstudiums habe ich den klassischen Weg der Steuerberaterausbildung absolviert und bin in diesem Bereich seit über 13 Jahren beratend tätig.</p>
  <p>Durch die Kombination meines umfassenden Wissens in der IT und der Wirtschaft habe ich schon immer gerne Unternehmen mit besonderes technischen oder digitalen Geschäftsmodellen beraten. Seit mehreren Jahren bin ich privat an der Blockchaintechnologie und dem Krypto-Universum interessiert und bereits seit dem Jahre 2017 ist dieses Thema auch Teil meiner fixen Beratungsfelder in der Steuerberatung.</p>
</div>

<section class="career">
  <div class="col left">
    <h2>Ausbildung</h2>
    <div class="item"><span class="year">2002</span><span>HTL - Matura mit Schwerpunkt IT und Betrieblicher Organisation</span></div>
    <div class="item"><span class="year gray">2009</span><span>Studium BWL mit Schwerpunkten Banking &amp; Finance sowie Kapitalmärkte</span></div>
    <div class="item"><span class="year">2012</span><span>Buchhalter &amp; Bilanzbuchhalterprüfung</span></div>
    <div class="item"><span class="year gray">2013</span><span>Angelobung zum Steuerberater</span></div>
  </div>
  <div class="col right">
    <h2>Beruflicher Werdegang</h2>
    <div class="item"><span class="year">2003-09</span><span>Selbständig tätig im IT Sektor</span></div>
    <div class="item"><span class="year gray">2009</span><span>Beratend tätig in der Steuerberatung / Wirtschaftsprüfung in verschiedenen Kanzleien. Zuletzt in leitender Funktion bei Alpenwert Prüfung Tirol</span></div>
    <div class="item"><span class="year">2022</span><span>Gründung der eigenen Kanzlei LM-Steuerberatung mit Fokus Krypto-Beratung.</span></div>
  </div>
  <div class="rule"></div>
  <div class="btn-profile">GO TO MY PRONET PROFILE <span class="sep"></span><span>PRONET</span></div>
</section>

<footer class="footer">
  <div class="brand-foot"><span class="mark"></span>LM STEUERBERATUNG</div>
  <p class="about">Ihrem Spezialisten bei allen steuerlichen Themen rund um Einkünfte &amp; Vermögen aus Krypto-Assets.</p>
  <p class="copy">Copyright © 2022 LM-Steuerberatung</p>

  <div class="quick">
    <h3>QUICK LINKS</h3>
    <ul>
      <li>›&nbsp;Home</li>
      <li>›&nbsp;Leistungen</li>
      <li>›&nbsp;Über mich</li>
      <li>›&nbsp;Impressum</li>
      <li>›&nbsp;Kontakt</li>
    </ul>
  </div>

  <div class="info">
    <h3>CONTACT INFORMATION</h3>
    <div class="row">
      <span class="icon"><svg width="18" height="16" viewBox="0 0 18 16" fill="none" stroke="#fff" stroke-width="1.6"><rect x="1" y="4" width="16" height="11" rx="2"/><path d="M1 6l8 5 8-5"/></svg></span>
      <div><div class="label">Email:</div><div class="value">office@lm-kryptosteuer.at</div></div>
    </div>
    <div class="row">
      <span class="icon"><svg width="18" height="18" viewBox="0 0 20 20" fill="#fff"><path d="M4 2l3 3-2 3c1 2 3 4 5 5l3-2 3 3-2 3C8 16 3 11 2 4z"/></svg></span>
      <div><div class="label">Phone:</div><div class="value">+43 512 000 471</div></div>
    </div>
    <div class="socials">Social Media: <span class="net">SOZIAL</span><span class="net">KURZNETZ</span><span class="net">PRONET</span></div>
  </div>
</footer>

</body>
</html>
```